qoBureau Business Card Design Project

We need a business card design for qoBureau. qoBureau is an underwriting agency. Underwriting agencies act on behalf of insurers, to underwrite insurance. We will be operating in specialised classes of insurance initially and looking to expand from there. We would like to see designs that incorporate our logo colours as well as a contrasting stand out colour - also we'd like the logo itself to be embossed on the card.

Industry/Entity Type

Insurance

Requirements
Must have
• Logo on front
Nice to have
• Logo solely featured on back of card
Should not have
• Please do not use comic cans font :)

```html
<!DOCTYPE html>
<html lang="en">
<head>
<meta charset="utf-8">
<title>qoBureau Business Card</title>
<link rel="stylesheet" href="https://fonts.googleapis.com/css2?family=Montserrat:wght@400;500&family=Tinos:wght@700&display=swap">
<style>
  :root {
    --page: #ffffff;
    --navy-deep: #051233;
    --navy: #0a2560;
    --blue-soft: #3a78b8;
    --band: #03103f;
    --divider: rgba(150, 185, 230, 0.45);
    --ink: #ffffff;
    --accent: #f2a52b;
  }
  * { margin: 0; padding: 0; box-sizing: border-box; }
  html, body {
    width: 1200px;
    height: 801px;
    overflow: hidden;
    background: var(--page);
  }
  .card {
    position: absolute;
    left: 30px;
    top: 76px;
    width: 1144px;
    height: 639px;
    border-radius: 70px;
    overflow: hidden;
    background:
      radial-gradient(ellipse at 78% 20%, rgba(90, 160, 220, 0.30), transparent 55%),
      radial-gradient(ellipse at 55% 70%, rgba(40, 100, 180, 0.30), transparent 60%),
      linear-gradient(160deg, var(--navy) 0%, var(--navy-deep) 100%);
    color: var(--ink);
  }
  .card__identity-panel {
    position: absolute;
    left: 0;
    top: 0;
    width: 579px;
    height: 573px;
    background: linear-gradient(170deg, rgba(60, 120, 190, 0.45) 0%, rgba(20, 60, 130, 0.35) 100%);
    border-right: 2px solid var(--divider);
  }
  .card__emblem-area {
    position: absolute;
    left: 105px;
    top: 102px;
    width: 384px;
    height: 428px;
    border-radius: 50%;
    background: radial-gradient(circle at 45% 45%, rgba(58, 120, 184, 0.55), rgba(26, 76, 143, 0.25) 60%, transparent 75%);
  }
  .card__name {
    position: absolute;
    left: 0;
    top: 296px;
    width: 664px;
    text-align: center;
    font-family: "Tinos", "Times New Roman", serif;
    font-weight: 700;
    font-size: 74px;
    line-height: 1;
    letter-spacing: 0.5px;
  }
  .card__job-title {
    position: absolute;
    left: 0;
    top: 354px;
    width: 664px;
    text-align: center;
    font-family: "Montserrat", Arial, sans-serif;
    font-size: 35px;
    line-height: 1.2;
  }
  .card__brand {
    position: absolute;
    right: 80px;
    top: 132px;
    display: flex;
    align-items: center;
    gap: 16px;
  }
  .card__brand-mark {
    width: 22px;
    height: 22px;
    border-radius: 50%;
    background: var(--accent);
  }
  .card__company {
    font-family: "Montserrat", Arial, sans-serif;
    font-weight: 500;
    font-size: 53px;
    line-height: 1.2;
    letter-spacing: 0.5px;
  }
  .card__contact {
    position: absolute;
    right: 80px;
    top: 254px;
    text-align: right;
    font-family: "Montserrat", Arial, sans-serif;
    font-size: 30px;
    line-height: 34px;
    list-style: none;
  }
  .card__contact .gap { margin-top: 14px; }
  .card__web-band {
    position: absolute;
    left: 0;
    bottom: 0;
    width: 100%;
    height: 66px;
    background: linear-gradient(180deg, var(--band), #020c33);
    border-top: 2px solid var(--accent);
    text-align: center;
    font-family: "Montserrat", Arial, sans-serif;
    font-size: 31px;
    line-height: 62px;
  }
</style>
</head>
<body>
  <div class="card">
    <div class="card__identity-panel">
      <div class="card__emblem-area" role="img" aria-label="Large soft blue globe emblem behind the name"></div>
    </div>

    <h1 class="card__name">Your Name</h1>
    <p class="card__job-title">Job Title</p>

    <div class="card__brand">
      <span class="card__brand-mark"></span>
      <h2 class="card__company">qoBureau</h2>
    </div>

    <ul class="card__contact">
      <li>yourname@yourcompany.com</li>
      <li>232 address Lane1,</li>
      <li>Address Lane 2,</li>
      <li class="gap">Mobile Number</li>
      <li>Phone Number</li>
      <li>Fax Number</li>
    </ul>

    <div class="card__web-band">www.yourcompany.com</div>
  </div>
</body>
</html>
```